Powepoint Templates From Logo

We need 3 Powerpoint templates for use in a variety of presentations we develop and customize. Primary uses of the powerpoint presentations are for printed "pitch books" describing our firm's capabilities and approach (a lot of words with some design elements that we have developed), printed presentations of the results of financial evaluations of our clients (lots of charts and graphs) and as the talking points for speeches.

The design needs to be professional and "solid" to establish that we are capable of selling your multi-million dollar business, but also be a little different to show that we are not just boring MBA's.

Our current website and other materials have been developed internally and leave a great deal to be desired. I have initiated this project to demonstrate how much our look can be improved and, if successful, I hope to do much bigger projects in the future.
Updates

This is my first project and I thaank you all for your participation. Since I am new to this, I don;t know if I am providing the help and feedback as I should. Please feel free to let me know how I can be a better customer.

Target Market(s)

professionals (lawyers, accountaants), business owners, business groups, technology people

Industry/Entity Type

Financial

Requirements
Must have
• our logo
a place where logo of client can be inserted if appropriate
templates for the following pages
title page
standard bullet narrative page
page for charts and graphs to mostly fill the page
Should not have a lot of dark solid color that has to be printed.

Nice to have
• something to perk up the color a little

```html
<!DOCTYPE html>
<html lang="en">
<head>
<meta charset="utf-8">
<title>Project Title Here</title>
<link rel="stylesheet" href="https://fonts.googleapis.com/css2?family=Oswald:wght@700&family=Arimo:wght@400;700&display=swap">
<style>
  :root {
    --navy: #0b2a5e;
    --sky: #8fb0e0;
    --pale: #c9dbf2;
    --mist: #eaf1fb;
    --ink: #111111;
    --white: #ffffff;
  }
  * { margin: 0; padding: 0; box-sizing: border-box; }
  html, body { width: 1200px; height: 900px; overflow: hidden; background: var(--white); }
  .slide { position: relative; width: 1200px; height: 900px; overflow: hidden; font-family: "Arimo", Arial, sans-serif; }
  .slide-frame { position: absolute; inset: 0; }
  .portrait {
    position: absolute; left: 88px; top: 17px; width: 120px; height: 146px;
    border: 3px solid var(--white); border-radius: 16px;
    background: linear-gradient(160deg, #b9c4cf 0%, #5c6875 55%, #23282f 100%);
    box-shadow: 0 1px 3px rgba(0,0,0,.35);
  }
  .slide-title {
    position: absolute; right: 22px; top: 28px;
    font-family: "Oswald", "Arial Narrow", sans-serif; font-weight: 700;
    font-size: 60px; line-height: 1; color: var(--navy); letter-spacing: .5px;
    white-space: nowrap;
  }
  .section-heading {
    position: absolute; left: 85px; top: 232px;
    font-size: 40px; font-weight: 700; color: var(--sky); letter-spacing: .3px;
  }
  .bullet-list { position: absolute; left: 88px; top: 300px; list-style: none; }
  .bullet-list li {
    position: relative; padding-left: 26px; height: 56px;
    font-size: 24px; line-height: 30px; color: var(--ink); white-space: nowrap;
  }
  .bullet-list li svg { position: absolute; left: 0; top: 8px; }
  .brand { position: absolute; left: 34px; top: 808px; display: flex; align-items: center; gap: 14px; }
  .brand-dot { width: 18px; height: 18px; border-radius: 50%; background: var(--navy); }
  .brand-name { font-size: 34px; font-weight: 400; color: var(--navy); line-height: 1; letter-spacing: 2px; }
  .page-number {
    position: absolute; right: 14px; bottom: 8px;
    font-size: 24px; color: var(--white);
  }
</style>
</head>
<body>
<main class="slide">
  <svg class="slide-frame" width="1200" height="900" viewBox="0 0 1200 900" aria-hidden="true">
    <polygon points="585,0 620,0 0,188 0,172" fill="var(--sky)"/>
    <polygon points="0,0 585,0 0,172" fill="var(--navy)"/>
    <line x1="210" y1="105" x2="1200" y2="105" stroke="var(--pale)" stroke-width="2"/>
    <line x1="0" y1="760" x2="1200" y2="760" stroke="var(--pale)" stroke-width="2"/>
    <rect x="0" y="884" width="1200" height="16" fill="var(--mist)"/>
    <polygon points="880,900 1200,798 1200,812 918,900" fill="var(--sky)"/>
    <polygon points="918,900 1200,812 1200,900" fill="var(--navy)"/>
  </svg>

  <div class="portrait" role="img" aria-label="Portrait photo of the presenter"></div>

  <h1 class="slide-title">PROJECT TITLE HERE</h1>

  <h2 class="section-heading">SUB TEXT HERE</h2>
  <ul class="bullet-list">
    <li><svg width="12" height="16" viewBox="0 0 12 16"><path d="M2 2 L9 8 L2 14" fill="none" stroke="var(--navy)" stroke-width="3"/></svg>Lorem ipsum dolor sit ipsum, Lorem ipsum dolor sit ipsum</li>
    <li><svg width="12" height="16" viewBox="0 0 12 16"><path d="M2 2 L9 8 L2 14" fill="none" stroke="var(--navy)" stroke-width="3"/></svg>Lorem ipsum dolor sit ipsum, Lorem ipsum dolor sit ipsum</li>
    <li><svg width="12" height="16" viewBox="0 0 12 16"><path d="M2 2 L9 8 L2 14" fill="none" stroke="var(--navy)" stroke-width="3"/></svg>Lorem ipsum dolor sit ipsum Lorem ipsum dolor sit ipsum</li>
    <li><svg width="12" height="16" viewBox="0 0 12 16"><path d="M2 2 L9 8 L2 14" fill="none" stroke="var(--navy)" stroke-width="3"/></svg>Lorem ipsum dolor sit ipsum, Lorem ipsum dolor sit ipsum</li>
    <li><svg width="12" height="16" viewBox="0 0 12 16"><path d="M2 2 L9 8 L2 14" fill="none" stroke="var(--navy)" stroke-width="3"/></svg>Lorem ipsum dolor sit ipsum, Lorem ipsum dolor sit ipsum</li>
    <li><svg width="12" height="16" viewBox="0 0 12 16"><path d="M2 2 L9 8 L2 14" fill="none" stroke="var(--navy)" stroke-width="3"/></svg>Lorem ipsum dolor sit ipsum Lorem ipsum dolor sit ipsum</li>
  </ul>

  <div class="brand">
    <div class="brand-dot"></div>
    <div class="brand-name">ASHFORD KELM</div>
  </div>

  <div class="page-number">PAGE 2 OF 2</div>
</main>
</body>
</html>
```